Home decoration company - sustainable wall panels

- I would need you to design 5-10 pages for my client's website.
- The design should have details of wall panels that are being sold on the website - movelterra.com.
- It should have wood + sustainability branding.
- please focus on using shapes of products that are being sold on the website and use them as design for branding

See more here
https://sheets.quorvix.net/d/7kpRtW2nLqZ8bYhMfGcVdXsJ4eTuA9wN3oHiKy5BzPl/edit?usp=sharing

Target Market(s)

people who are want sustainable home/business wall decor

Industry/Entity Type

Interior Decoration

Logo Text

Movel Terra (for favicon, "MT")

Number of Pages Required

5+ page

Font styles to use
Serif
Sans Serif

Requirements
Must have
• - details of products that are being sold on the website movelterra.com (you will see there are different wall panel shapes)
- great creative design ideas
- follow instructions from here https://sheets.quorvix.net/d/7kpRtW2nLqZ8bYhMfGcVdXsJ4eTuA9wN3oHiKy5BzPl/edit?usp=sharing
- the design must be at least 2 levels above the current one on movelterra.com
- use photos from here https://files.quorvix.net/folders/5tWmQeRb8YuNc2XkLpAsDv3ZhGj7FiO-?usp=sharing
Nice to have
• - it would be nice if you would give your own creative suggestions
Should not have
• - should not look like it's a 1990s website

```html
<!DOCTYPE html>
<html lang="en">
<head>
<meta charset="utf-8">
<title>About Movel Terra</title>
<link href="https://fonts.googleapis.com/css2?family=Oswald:wght@500;600;700&family=Montserrat:wght@400;500;600;700&display=swap" rel="stylesheet">
<style>
:root{
  --bar:#2b1607;
  --brown:#7b3f0a;
  --heading:#2e1605;
  --text:#3a3a3a;
  --muted:#555;
  --star:#f39c12;
  --footer:#efedeb;
  --field:#e4e3e2;
  --gold:#e8b628;
}
*{margin:0;padding:0;box-sizing:border-box}
html,body{width:1200px;height:2480px;overflow:hidden;background:#fff}
body{font-family:"Montserrat",sans-serif;color:var(--text);position:relative}
.abs{position:absolute}
.display{font-family:"Oswald",sans-serif;font-weight:700;color:var(--heading);letter-spacing:-.5px;text-transform:uppercase}

.topbar{left:0;top:0;width:1200px;height:29px;background:var(--bar);color:#fff;font-size:11px;display:flex;align-items:center;justify-content:space-between;padding:0 89px}
.topbar .info{display:flex;gap:22px;align-items:center}
.topbar .info span{display:flex;align-items:center;gap:6px}

.nav{left:0;top:29px;width:1200px;height:70px;background:#fff;display:flex;align-items:center;justify-content:space-between;padding:0 89px}
.brand{font-weight:600;color:var(--brown);font-size:17px;display:flex;align-items:center;gap:8px}
.brand .mark{width:14px;height:14px;background:var(--brown)}
.menu{display:flex;gap:28px;font-family:"Oswald",sans-serif;font-weight:500;font-size:13px;color:var(--heading);text-transform:uppercase}
.menu .active{color:var(--brown)}

.hero{left:0;top:99px;width:1200px;height:217px;background:linear-gradient(100deg,#3b2a22 0%,#5a3d28 35%,#8a5a32 65%,#5e3b1e 100%)}
.hero-title{left:0;width:1200px;top:180px;line-height:44px;text-align:center;color:#fff;font-size:38px}
.hero-sub{left:0;width:1200px;top:226px;line-height:26px;text-align:center;color:#fff;font-weight:600;font-size:19px}

.section-title{left:0;width:1200px;text-align:center;font-size:34px;line-height:44px}
.feature{width:270px;text-align:center}
.feature .icon{width:96px;height:96px;background:var(--brown);margin:0 auto;display:flex;align-items:center;justify-content:center}
.feature h3{font-size:26px;line-height:34px;margin-top:20px}
.feature p{font-size:13px;line-height:20px;color:var(--muted);margin-top:4px}

.team-back{left:0;top:768px;width:330px;height:547px;background:linear-gradient(180deg,#4b3626,#6b4f38 50%,#3e2c1f)}
.team-photo{left:146px;top:832px;width:355px;height:413px;background:linear-gradient(135deg,#9a9490 0%,#6d5f55 45%,#c2a88a 75%,#8a7766 100%)}
.team-title{left:570px;top:902px;font-size:38px;line-height:44px}
.team-text{left:570px;top:952px;width:490px;font-size:14.2px;line-height:20.5px;color:#333}

.arrows{left:1068px;top:1384px;display:flex;gap:14px}
.card{top:1445px;width:333px;height:203px;background:#fff;box-shadow:0 6px 22px rgba(0,0,0,.09);padding:44px 30px 0 36px}
.card p{font-size:14px;line-height:21.5px;color:#333}
.card .stars{color:var(--star);font-size:15px;letter-spacing:3px;margin-top:2px;line-height:18px}
.card .name{font-weight:700;color:var(--brown);font-size:16px;letter-spacing:.5px}

.retailer{left:0;width:1200px;top:1688px;text-align:center;font-weight:700;color:var(--brown);font-size:40px;line-height:52px;letter-spacing:-.5px}
.btn{background:var(--brown);color:#fff;font-weight:700;text-transform:uppercase;display:flex;align-items:center;justify-content:center}
.shop{left:535px;top:1766px;width:129px;height:36px;font-size:14px}

.warranty-title{left:87px;top:1866px;font-size:38px;line-height:44px}
.warranty-text{left:87px;top:1912px;font-size:16px;line-height:22px;color:#333}
.badge{left:984px;top:1833px}

.footer{left:0;top:1987px;width:1200px;height:493px;background:var(--footer)}
.f-brand{left:89px;top:2150px;font-weight:600;color:var(--brown);font-size:34px;display:flex;align-items:center;gap:12px}
.f-brand .mark{width:26px;height:26px;background:var(--brown)}
.f-head{font-family:"Oswald",sans-serif;font-weight:600;font-size:24px;line-height:32px;color:var(--heading);text-transform:uppercase;top:2096px}
.f-list{top:2136px;font-size:13px;color:#444;line-height:24px;list-style:none}
.f-contact{left:541px;top:2136px;font-size:13px;color:#444;line-height:20px}
.f-contact .row{display:flex;gap:8px;margin-bottom:4px}
.socials{left:549px;top:2215px;display:flex;gap:16px}
.socials span{width:14px;height:14px;border-radius:50%;background:var(--brown)}
.field{left:829px;width:242px;background:var(--field);font-size:11px;color:#555;padding:10px 15px}
.submit{left:830px;top:2319px;width:91px;height:30px;font-size:12px}
.rule{left:89px;top:2419px;width:1022px;height:1px;background:#cfcac5}
.totop{left:1132px;top:2402px;width:34px;height:34px;border-radius:50%;background:var(--bar);display:flex;align-items:center;justify-content:center}
.copy{left:0;width:1200px;top:2443px;text-align:center;font-size:16px;color:#333}
</style>
</head>
<body>

<header class="abs topbar">
  <span>Ordering larger quantities? Call us.</span>
  <div class="info">
    <span><svg width="10" height="10" viewBox="0 0 24 24"><path fill="#c9853e" d="M6.6 10.8a15 15 0 0 0 6.6 6.6l2.2-2.2c.3-.3.7-.4 1-.2 1.1.4 2.3.6 3.6.6.6 0 1 .4 1 1V20c0 .6-.4 1-1 1A17 17 0 0 1 3 4c0-.6.4-1 1-1h3.5c.6 0 1 .4 1 1 0 1.3.2 2.5.6 3.6.1.3 0 .7-.2 1z"/></svg>phone number :&nbsp; +1 555 014 2760</span>
    <span><svg width="11" height="9" viewBox="0 0 24 18"><path fill="#c9853e" d="M0 0h24v18H0z"/><path fill="none" stroke="#2b1607" stroke-width="2" d="M1 1l11 8 11-8"/></svg>Email : hello@movelterra.com, orders@movelterra.com</span>
  </div>
</header>

<nav class="abs nav">
  <div class="brand"><span class="mark"></span>Movel Terra</div>
  <div class="menu">
    <span>Home</span><span>Wall Paneling</span><span>Door</span><span>Cutting Boards</span><span>Table Tops</span><span class="active">About Us</span><span>Contact Us</span>
  </div>
</nav>

<div class="abs hero" role="img" aria-label="Trade show booth with reclaimed wood wall panels and visitors"></div>
<h1 class="abs display hero-title">About Movel Terra</h1>
<p class="abs hero-sub">100% Sustainable. 100% Hand Crafted. 100% Unique.</p>

<h2 class="abs display section-title" style="top:404px">Why Choose Us</h2>

<div class="abs feature" style="left:120px;top:493px">
  <div class="icon"><svg width="58" height="58" viewBox="0 0 58 58" fill="none" stroke="#fff" stroke-width="4" stroke-linejoin="round"><path d="M10 48C10 22 26 10 50 8c0 26-14 40-40 40z"/><path d="M12 46L38 20"/></svg></div>
  <h3 class="display">Sustainable</h3>
  <p>Every wall panel is cut from reclaimed boat and teak wood, saving old timber from waste.</p>
</div>
<div class="abs feature" style="left:465px;top:493px">
  <div class="icon"><svg width="60" height="60" viewBox="0 0 60 60" fill="#fff"><path d="M20 6l11 6v12l-11 6-11-6V12z"/><path d="M42 18l11 6v12l-11 6-11-6V24z" opacity=".8"/><path d="M20 30l11 6v12l-11 6-11-6V36z" opacity=".9"/></svg></div>
  <h3 class="display">Hand Crafted</h3>
  <p>Hexagon, chevron and block panels are cut, sanded and fitted by artisans in East Java.</p>
</div>
<div class="abs feature" style="left:805px;top:493px">
  <div class="icon"><svg width="60" height="60" viewBox="0 0 60 60" fill="none" stroke="#fff" stroke-width="5" stroke-linejoin="miter"><path d="M6 22l24-14 24 14"/><path d="M6 36l24-14 24 14"/><path d="M6 50l24-14 24 14"/></svg></div>
  <h3 class="display">Unique</h3>
  <p>No two panels share the same grain, colour or story, so each wall you build is unique.</p>
</div>

<div class="abs team-back" role="img" aria-label="Stacked reclaimed timber in a dark workshop"></div>
<div class="abs team-photo" role="img" aria-label="Artisan carving a reclaimed wood panel by hand"></div>
<h2 class="abs display team-title">Our Team</h2>
<p class="abs team-text">At Movel Terra our goal is to provide the highest quality repurposed interior décor products and housewares that reflect not only your aesthetic, but that have a story. Having traveled the world, we know the feeling something special acquired during a trip brings. At first perhaps just a memento, but after time a deeper memory and conversation piece that brings you back to its origin again. Though you may never have visited East Java, we think our products will create an unspoken link between you and the artisans and fisherman who put their heart into our products. Their masterful handiwork, along with our love for pieces full of rustic and vintage charm inspired us to share these products with you. We are proud that our work provides local fisherman and craftsmen a sustainable income and continue to think of new products that will inspire our customers.</p>

<h2 class="abs display section-title" style="top:1368px">Verified Reviews For Our Products</h2>
<div class="abs arrows">
  <svg width="16" height="16" viewBox="0 0 16 16"><path d="M10 3L5 8l5 5" fill="none" stroke="#222" stroke-width="2.2"/></svg>
  <svg width="16" height="16" viewBox="0 0 16 16"><path d="M6 3l5 5-5 5" fill="none" stroke="#222" stroke-width="2.2"/></svg>
</div>

<div class="abs card" style="left:89px">
  <p>The hexagon wall panels went up in one afternoon. The reclaimed grain and colour make our living room feel warm.</p>
  <div class="stars">★★★★★</div><div class="name">Dana Wells</div>
</div>
<div class="abs card" style="left:433px">
  <p>Our chevron feature wall is the first thing guests notice. Each panel arrived well packed and ready to mount.</p>
  <div class="stars">★★★★★</div><div class="name">Dana Wells</div>
</div>
<div class="abs card" style="left:776px">
  <p>We used the mixed block panels behind our café counter. Solid wood, real character and a great sustainable story.</p>
  <div class="stars">★★★★★</div><div class="name">Dana Wells</div>
</div>

<div class="abs retailer">Hearthline</div>
<div class="abs btn shop">Shop Now</div>

<h2 class="abs display warranty-title">Our Products Have A 10 Year Warranty</h2>
<p class="abs warranty-text">Each purchase backed by a limited 10 year warranty for residential applications.</p>
<svg class="abs badge" width="128" height="128" viewBox="0 0 128 128"><circle cx="64" cy="64" r="62" fill="var(--gold)"/><circle cx="64" cy="64" r="44" fill="#3a2a10"/><circle cx="64" cy="64" r="30" fill="var(--gold)"/></svg>

<footer class="abs footer" role="img" aria-label="Faint pattern of wood tree-ring cross sections"></footer>
<div class="abs f-brand"><span class="mark"></span>Movel Terra</div>

<h3 class="abs f-head" style="left:350px">Navigation</h3>
<ul class="abs f-list" style="left:350px">
  <li>Home</li><li>Wall panels</li><li>Doors</li><li>Cutting boards</li><li>About us</li>
</ul>

<h3 class="abs f-head" style="left:541px">Contact Us</h3>
<div class="abs f-contact">
  <div class="row"><svg width="13" height="13" viewBox="0 0 24 24" style="margin-top:3px"><path fill="var(--brown)" d="M6.6 10.8a15 15 0 0 0 6.6 6.6l2.2-2.2c.3-.3.7-.4 1-.2 1.1.4 2.3.6 3.6.6.6 0 1 .4 1 1V20c0 .6-.4 1-1 1A17 17 0 0 1 3 4c0-.6.4-1 1-1h3.5c.6 0 1 .4 1 1 0 1.3.2 2.5.6 3.6.1.3 0 .7-.2 1z"/></svg><span>Phone number +1 555 014 2760</span></div>
  <div class="row"><svg width="13" height="11" viewBox="0 0 24 18" style="margin-top:4px"><path fill="var(--brown)" d="M0 0h24v18H0z"/><path fill="none" stroke="#efedeb" stroke-width="2" d="M1 1l11 8 11-8"/></svg><span>Email us : hello@movelterra.com,<br>orders@movelterra.com</span></div>
</div>
<div class="abs socials"><span></span><span></span><span></span></div>

<h3 class="abs f-head" style="left:826px">Contact Form</h3>
<div class="abs field" style="top:2141px;height:32px">Name</div>
<div class="abs field" style="top:2175px;height:30px">Email</div>
<div class="abs field" style="top:2213px;height:98px">Message</div>
<div class="abs btn submit">Submit</div>

<div class="abs rule"></div>
<div class="abs totop"><svg width="10" height="8" viewBox="0 0 10 8"><path d="M1 6l4-4 4 4" fill="none" stroke="#fff" stroke-width="1.8"/></svg></div>
<p class="abs copy">Copyright 2020 | All Rights Reserved</p>

</body>
</html>
```